Meridian Crestline Motors *

Professional business cards for our auto wholesale dealership.

Target Market(s)

New and used cars sales managers and middle class to higher end private party buyers.

Industry/Entity Type

Automotive

Contact Information for Business Card

Meridian Crestline Motors
Darnell R Okonski
Owner
(555) 304-6618
mercrestmotors@quillbox.example
Dealer Lic # 48265

Logo Text

Meridian Crestline Motors, Mer Crest Motors, MCM, etc

Font styles to use
Serif
Sans Serif

Colors

Designer to choose colors to be used in the design.

Requirements
Must have
• A professional, but not pretentious, look
Nice to have
• It might be nice to see "MCM" in a shape form i.e. circle, triangle, etc in the corner or background somehwere
Should not have
• bright "girly" colors

```html
<!DOCTYPE html>
<html lang="en">
<head>
<meta charset="utf-8">
<title>Meridian Crestline Motors — Business Card</title>
<link rel="stylesheet" href="https://fonts.googleapis.com/css2?family=Open+Sans:wght@400;600;700;800&display=swap">
<style>
  :root {
    --canvas: #2b2d31;
    --card-dark: #262c36;
    --card-dark-edge: #1d222a;
    --card-light: #e9e9e9;
    --card-light-edge: #c9c9c9;
    --lime: #b5d416;
    --lime-deep: #95b80c;
    --ink-dark: #232830;
    --ink-light: #f2f4f5;
    --rule: #2c3038;
    --photo-hi: #d8d9db;
    --photo-lo: #7b7e84;
  }
  * { box-sizing: border-box; margin: 0; padding: 0; }
  html, body {
    width: 1200px; height: 1200px; overflow: hidden;
    background: var(--canvas);
    font-family: "Open Sans", Arial, sans-serif;
  }
  .sheet {
    position: relative; width: 1200px; height: 1200px;
    display: flex; flex-direction: column; align-items: center; justify-content: center; gap: 44px;
  }
  .card {
    position: relative; width: 900px; height: 514px;
    border-radius: 28px; overflow: hidden;
    box-shadow: 0 18px 40px rgba(0,0,0,.45);
  }

  /* Back face */
  .card--back { background: linear-gradient(160deg, #f4f4f4 0%, var(--card-light) 55%, var(--card-light-edge) 100%); }
  .card--back .brand { position: absolute; left: 40px; top: 34px; }
  .card--back .rule {
    position: absolute; left: 470px; right: 0; top: 150px;
    height: 3px; background: var(--rule);
  }
  .fleet-photo {
    position: absolute; left: 40px; top: 120px; width: 700px; height: 370px;
    border-radius: 18px;
    background: radial-gradient(ellipse at 40% 45%, var(--photo-hi) 0%, #a9abaf 45%, var(--photo-lo) 100%);
    opacity: .9;
  }

  /* Brand lockup */
  .brand { display: flex; align-items: center; gap: 16px; }
  .brand__mark {
    width: 74px; height: 74px; border-radius: 50%;
    background: var(--lime); flex: none;
  }
  .brand__name {
    color: var(--lime); font-weight: 800; font-size: 30px; line-height: 1.05;
    text-transform: uppercase; letter-spacing: .5px;
  }

  /* Front face */
  .card--front { background: linear-gradient(150deg, #2e3541 0%, var(--card-dark) 50%, var(--card-dark-edge) 100%); }
  .card--front .brand { position: absolute; left: 90px; top: 70px; flex-direction: column; align-items: flex-start; gap: 14px; }
  .card--front .brand__mark { margin-left: 150px; width: 84px; height: 84px; }
  .lime-strip {
    position: absolute; left: 0; bottom: 0; width: 520px; height: 44px;
    background: linear-gradient(90deg, var(--lime-deep), var(--lime));
    border-top-right-radius: 24px;
  }
  .name-plate {
    position: absolute; right: 0; top: 190px; width: 390px; height: 96px;
    background: linear-gradient(90deg, #c7e31c, var(--lime-deep));
    border-radius: 22px 0 0 22px;
    display: flex; flex-direction: column; justify-content: center; align-items: center;
    color: var(--ink-dark);
  }
  .name-plate__name { font-size: 32px; font-weight: 600; line-height: 1.1; }
  .name-plate__role { font-size: 22px; font-weight: 600; }
  .contact {
    position: absolute; right: 46px; top: 318px;
    list-style: none; display: flex; flex-direction: column; gap: 16px;
    color: var(--ink-light); font-size: 25px; text-align: right;
  }
  .contact__item { display: flex; align-items: center; justify-content: flex-end; gap: 16px; }
  .contact__icon { width: 28px; height: 28px; flex: none; }
  .contact__spacer { width: 28px; flex: none; }
</style>
</head>
<body>
<main class="sheet">

  <section class="card card--back" aria-label="Card back">
    <div class="fleet-photo" role="img" aria-label="Photo of three silver sedans parked in a row"></div>
    <div class="brand">
      <span class="brand__mark"></span>
      <span class="brand__name">Meridian Crestline<br>Motors</span>
    </div>
    <div class="rule"></div>
  </section>

  <section class="card card--front" aria-label="Card front">
    <div class="brand">
      <span class="brand__mark"></span>
      <span class="brand__name">Meridian Crestline<br>Motors</span>
    </div>

    <div class="name-plate">
      <span class="name-plate__name">Darnell R Okonski</span>
      <span class="name-plate__role">Owner</span>
    </div>

    <ul class="contact">
      <li class="contact__item">
        <span>(555) 304-6618</span>
        <svg class="contact__icon" viewBox="0 0 24 24" aria-hidden="true">
          <path fill="var(--lime)" d="M6.6 10.8a15.1 15.1 0 0 0 6.6 6.6l2.2-2.2c.3-.3.7-.4 1-.2 1.1.4 2.3.6 3.6.6.6 0 1 .4 1 1V20c0 .6-.4 1-1 1A17 17 0 0 1 3 4c0-.6.4-1 1-1h3.5c.6 0 1 .4 1 1 0 1.3.2 2.5.6 3.6.1.3 0 .7-.2 1z"/>
        </svg>
      </li>
      <li class="contact__item">
        <span>mercrestmotors@quillbox.example</span>
        <svg class="contact__icon" viewBox="0 0 24 24" aria-hidden="true">
          <rect x="2" y="5" width="20" height="14" rx="1.5" fill="none" stroke="var(--lime)" stroke-width="2"/>
          <path d="M2.5 6 12 13l9.5-7M2.5 18l7-6M21.5 18l-7-6" fill="none" stroke="var(--lime)" stroke-width="1.8"/>
        </svg>
      </li>
      <li class="contact__item">
        <span>Dealer Lic # 48265</span>
        <span class="contact__spacer"></span>
      </li>
    </ul>

    <div class="lime-strip"></div>
  </section>

</main>
</body>
</html>
```